Visitenkarten-Design für virtuelle Jobmesse & Jobbörse für Soldaten
Zielgruppe
Die KVL GmbH ist ein Unternehmen das zwei Hauptprodukte betreibt! Zum einen Jobbörse für Soldaten unter www.laufbahnwechsel-beispiel.de und zum anderen eine virtuelle Jobmesse für Soldaten unter www.merivon-beispiel.de , die wir zweimal im Jahr veranstalten.
Aufgabenstellung
Wir haben ja die beiden Produkte Laufbahnwechsel.de und die Merivon, für die bereits jeweils ein separtes Logo besteht! Diese finden Sie im Anhang! Beide werden doch jedoch von einem Unternehmen, der KVL GmbH betrieben! Aktuell nutzen wir eine Visitenkarte mit dem Logo von KVL und eine mit dem Logo der MERIVON. Gerade im Hinblick darauf, dass wir zukünftig auch weiter Plattformen in unser Portfolio aufnehmen, möchte ich hier unsere V-Karten flexibler gestalten!
Ziel soll es also sein, eine Visitenkarte zu gestalten, auf dem klar wird, dass der Mitarbeiter von der KVL GmbH kommt, die KVL GmbH aber unterschiedliche Produkte betreibt.
Im Anhang finden Sie:
1. Das Logo von KVL
2. Das Logo von Merivon
3. Die aktuelle V-Karte von KVL
4. Die aktuelle V-Karte von MERIVON
Vielleicht ein kleiner Anreiz: Aktuell nutzen wir auch zwei getrennte Geschäftspapiere. Das von www.laufbahnwechsel-beispiel.de lade ich einmal hoch! Der Designer, der auch die Visitenkarte erstellt, erhällt im Anschluss den 1:1 Auftrag in Höhe von 200 Euro für die Erstellung des Geschäftspapiers! Wenn Sie jetzt schon einen Vorschlag für das Geschäftspapier einreichen, erhöht das natürlich Ihre Chancen, wobei ich verspreche, dass wir im Falle eine Annahme das 1:1 im Anschluß dennoch starten werden!

```html
<!DOCTYPE html>
<html lang="de">
<head>
<meta charset="utf-8">
<title>KVL GmbH – Geschäftsausstattung</title>
<link href="https://fonts.googleapis.com/css2?family=Arimo:wght@400;700&display=swap" rel="stylesheet">
<style>
  :root{
    --bg:#f7ebdb;
    --paper:#ffffff;
    --blue:#224b8b;
    --blue-light:#8fa6cf;
    --green:#3d5a2a;
    --grey-line:#8a8f98;
    --text:#444444;
    --text-soft:#777777;
    --shadow:4px 5px 7px rgba(60,50,40,.45);
  }
  *{box-sizing:border-box;margin:0;padding:0}
  html,body{width:1200px;height:1000px;overflow:hidden;background:var(--bg)}
  body{font-family:"Arimo",Arial,sans-serif;color:var(--text)}
  .canvas{position:relative;width:1200px;height:1000px;background:var(--bg)}
  .piece{position:absolute;background:var(--paper);box-shadow:var(--shadow);overflow:hidden}
  .abs{position:absolute;white-space:nowrap}
  .center{transform:translateX(-50%);text-align:center}
  .right{text-align:right}

  .rule{position:absolute;left:0;right:0;height:5px;border-top:2px solid var(--blue);border-bottom:1px solid var(--grey-line)}
  .rule.on-blue{border-top-color:var(--blue-light);border-bottom-color:#b9c2d2}

  .brand-name{position:absolute;transform:translate(-50%,-50%);background:var(--paper);color:var(--blue);font-weight:700;padding:0 3px;white-space:nowrap}
  .brand-name.on-blue{background:var(--blue);color:#e6e9ef}

  .company{font-weight:700;color:var(--text)}
  .product{display:flex;align-items:center;gap:3px;transform:translateX(-50%);color:var(--green);font-weight:700;letter-spacing:.04em}
  .product .dot{display:inline-block;border-radius:50%;background:var(--green)}
  .product-url{color:var(--green);font-weight:700}
  .product-note{color:var(--text);font-weight:700}
  .label{color:var(--blue)}

  .band{position:absolute;left:0;right:0;bottom:0}
  .band svg{display:block}
  .band-text{position:absolute;top:50%;transform:translate(-50%,-50%);color:#fff;font-weight:700;white-space:nowrap}

  /* letterhead */
  .letterhead{left:77px;top:63px;width:419px;height:594px}
  .letterhead .footer-rule{position:absolute;left:0;right:0;top:549px;border-top:1px solid #cfcfcf}
  .letterhead .legal{position:absolute;left:209px;transform:translateX(-50%);font-size:5px;color:var(--text-soft);white-space:nowrap}

  /* business cards */
  .card-front{left:543px;top:56px;width:292px;height:189px}
  .card-back{left:862px;top:55px;width:291px;height:189px;background:var(--blue)}
  .person-name{font-size:16px;color:var(--blue)}
  .person-role{font-size:8.5px;color:var(--text);letter-spacing:.05em}

  /* envelopes */
  .envelope-window{left:652px;top:273px;width:439px;height:223px}
  .envelope-front{left:652px;top:510px;width:439px;height:224px}
  .envelope-back{left:652px;top:746px;width:439px;height:220px}
  .envelope-open{left:68px;top:684px;width:440px;height:282px;background:transparent;box-shadow:none;overflow:visible}
  .envelope-open svg{position:absolute;left:0;top:0;filter:drop-shadow(4px 5px 4px rgba(60,50,40,.4))}
</style>
</head>
<body>
<div class="canvas">

  <!-- Letterhead -->
  <section class="piece letterhead">
    <div class="rule" style="top:31px"></div>
    <span class="brand-name" style="left:364px;top:34px;font-size:7px">Laufbahnwechsel.de</span>
    <span class="abs company center" style="left:364px;top:50px;font-size:9px">KVL GmbH</span>
    <span class="abs product" style="left:364px;top:74px;font-size:7.5px"><i class="dot" style="width:6px;height:6px"></i>MERIVON</span>
    <span class="abs product-url center" style="left:364px;top:94px;font-size:6.5px">Merivon.de</span>
    <span class="abs product-note center" style="left:361px;top:104px;font-size:4.5px">ist eine Marke der KVL GmbH</span>

    <div class="abs right" style="right:23px;top:123px;font-size:5px;line-height:8px">
      <div class="company">KVL GMBH</div>
      <div>Lindenweg 7</div>
      <div>86650 Musterfeld</div>
    </div>
    <div class="abs right" style="right:23px;top:149px;font-size:5px;line-height:9.4px">
      <div><span class="label">Telef.:</span>&nbsp; 08431 - 552 19 07</div>
      <div><span class="label">Mobil.:</span> 0171 - 384 22 915</div>
      <div><span class="label">E.:</span> j.berger@merivon-beispiel.de</div>
      <div><span class="label">E.:</span> j.berger@laufbahnwechsel-beispiel.de</div>
    </div>

    <svg class="abs" style="left:36px;top:78px" width="176" height="88" viewBox="0 0 176 88" aria-hidden="true">
      <g fill="none" stroke="#9a9a9a" stroke-width="0.8">
        <path d="M1 14 V8 Q1 1 8 1 H15"/>
        <path d="M161 1 H168 Q175 1 175 8 V14"/>
        <path d="M1 73 V80 Q1 87 8 87 H15"/>
        <path d="M161 87 H168 Q175 87 175 80 V73"/>
      </g>
    </svg>
    <span class="abs" style="left:60px;top:85px;font-size:5px"><b>KVL GMBH</b> &bull; Lindenweg 7 &bull; 86650 Musterfeld</span>

    <div class="footer-rule"></div>
    <span class="legal" style="top:555px">Bank: Musterbank Rheinland &bull; IBAN: DE 12 3456 7800 0009 8765 &bull; BIC-Swift: MUSTDE00XXX</span>
    <span class="legal" style="top:565px">Amtsgericht Musterstadt &bull; Handelsregister: 012345 &bull; USt.-ID-Nr.: DE000111222</span>

    <div class="band">
      <svg width="419" height="17" viewBox="0 0 419 17" aria-hidden="true">
        <polygon points="0,0 199,0 192,17 0,17" fill="var(--green)"/>
        <g fill="#8c8c8c">
          <polygon points="203,0 207,0 200,17 196,17"/>
          <polygon points="211,0 215,0 208,17 204,17"/>
          <polygon points="219,0 223,0 216,17 212,17"/>
        </g>
        <polygon points="229,0 419,0 419,17 222,17" fill="var(--blue)"/>
      </svg>
      <span class="band-text" style="left:99px;font-size:8.5px">www.merivon-beispiel.de</span>
      <span class="band-text" style="left:322px;font-size:8.5px">www.laufbahnwechsel-beispiel.de</span>
    </div>
  </section>

  <!-- Business card front -->
  <section class="piece card-front">
    <span class="abs person-name" style="left:26px;top:14px">Jonas Berger</span>
    <span class="abs person-role" style="left:26px;top:30px">Geschäftsführer</span>
    <div class="rule" style="top:41px"></div>
    <span class="brand-name" style="left:229px;top:44px;font-size:9px">Laufbahnwechsel.de</span>
    <span class="abs company center" style="left:227px;top:70px;font-size:11.5px">KVL GmbH</span>
    <span class="abs product" style="left:227px;top:103px;font-size:10px"><i class="dot" style="width:8px;height:8px"></i>MERIVON</span>
    <span class="abs product-url center" style="left:227px;top:132px;font-size:9.5px">Merivon.de</span>
    <span class="abs product-note center" style="left:224px;top:147px;font-size:6.5px">ist eine Marke der KVL GmbH</span>

    <div class="abs" style="left:26px;top:55px;font-size:8.5px;line-height:11.5px">
      <div class="company">KVL GMBH</div>
      <div>Lindenweg 7</div>
      <div>86650 Musterfeld</div>
    </div>
    <div class="abs" style="left:17px;top:98px;font-size:9px;line-height:14px">
      <div><span class="label" style="display:inline-block;width:52px">Telefon.:</span>08431 - 552 19 07</div>
      <div><span class="label" style="display:inline-block;width:52px">Mobil.:</span>0171 - 384 22 915</div>
    </div>
    <div class="abs" style="left:17px;top:128px;font-size:7.5px;line-height:14px">
      <div><span class="label">E.:</span> j.berger@laufbahnwechsel-beispiel.de</div>
      <div><span class="label">E.:</span> j.berger@merivon-beispiel.de</div>
    </div>

    <div class="band">
      <svg width="292" height="18" viewBox="0 0 292 18" aria-hidden="true">
        <polygon points="0,0 131,0 124,18 0,18" fill="var(--green)"/>
        <g fill="#8c8c8c">
          <polygon points="134,0 138,0 131,18 127,18"/>
          <polygon points="142,0 146,0 139,18 135,18"/>
          <polygon points="150,0 154,0 147,18 143,18"/>
        </g>
        <polygon points="160,0 292,0 292,18 153,18" fill="var(--blue)"/>
      </svg>
      <span class="band-text" style="left:62px;font-size:7.5px">www.merivon-beispiel.de</span>
      <span class="band-text" style="left:224px;font-size:7px">www.laufbahnwechsel-beispiel.de</span>
    </div>
  </section>

  <!-- Business card back -->
  <section class="piece card-back">
    <div class="rule on-blue" style="top:71px"></div>
    <span class="brand-name on-blue" style="left:146px;top:74px;font-size:17px;padding:0 6px">Laufbahnwechsel.de</span>
    <span class="abs product" style="left:146px;top:126px;font-size:14px;color:#d8dce3"><i class="dot" style="width:11px;height:11px;background:#d8dce3"></i>MERIVON</span>
  </section>

  <!-- Envelope with window -->
  <section class="piece envelope-window">
    <div class="rule" style="top:31px"></div>
    <span class="brand-name" style="left:64px;top:34px;font-size:5.5px">Laufbahnwechsel.de</span>
    <span class="abs company center" style="left:63px;top:48px;font-size:7.5px">KVL GmbH</span>
    <span class="abs product" style="left:63px;top:70px;font-size:6px"><i class="dot" style="width:5px;height:5px"></i>MERIVON</span>
    <span class="abs product-url center" style="left:63px;top:87px;font-size:5.5px">Merivon.de</span>
    <span class="abs product-note center" style="left:62px;top:97px;font-size:4px">ist eine Marke der KVL GmbH</span>
    <span class="abs" style="left:95px;top:38px;font-size:6.5px"><b>KVL GMBH</b> Lindenweg 7 &bull; 86650 Musterfeld</span>

    <div class="band">
      <svg width="439" height="17" viewBox="0 0 439 17" aria-hidden="true">
        <polygon points="0,0 205,0 198,17 0,17" fill="var(--green)"/>
        <g fill="#8c8c8c">
          <polygon points="209,0 213,0 206,17 202,17"/>
          <polygon points="217,0 221,0 214,17 210,17"/>
          <polygon points="225,0 229,0 222,17 218,17"/>
        </g>
        <polygon points="240,0 439,0 439,17 233,17" fill="var(--blue)"/>
      </svg>
      <span class="band-text" style="left:103px;font-size:9px">www.merivon-beispiel.de</span>
      <span class="band-text" style="left:336px;font-size:8.5px">www.laufbahnwechsel-beispiel.de</span>
    </div>
  </section>

  <!-- Envelope front with sender block -->
  <section class="piece envelope-front">
    <div class="rule" style="top:137px"></div>
    <span class="brand-name" style="left:310px;top:140px;font-size:5.5px">Laufbahnwechsel.de</span>
    <span class="abs company center" style="left:309px;top:153px;font-size:7.5px">KVL GmbH</span>
    <span class="abs product" style="left:309px;top:173px;font-size:6px"><i class="dot" style="width:5px;height:5px"></i>MERIVON</span>
    <span class="abs product-url center" style="left:309px;top:191px;font-size:5.5px">Merivon.de</span>
    <span class="abs product-note center" style="left:308px;top:200px;font-size:4px">ist eine Marke der KVL GmbH</span>
    <div class="abs right" style="right:28px;top:180px;font-size:6.5px;line-height:9.5px">
      <div class="company" style="font-size:6px">KVL GMBH</div>
      <div>Lindenweg 7</div>
      <div>86650 Musterfeld</div>
    </div>
  </section>

  <!-- Envelope back with closed flap -->
  <section class="piece envelope-back">
    <svg class="abs" style="left:0;top:0" width="439" height="70" viewBox="0 0 439 70" aria-hidden="true">
      <path d="M0 0 H439 L405 56 Q399 63 390 63 H49 Q40 63 35 56 Z" fill="var(--blue)"/>
      <rect x="12" y="30" width="415" height="1.5" fill="var(--blue-light)"/>
      <rect x="12" y="33" width="415" height="0.8" fill="#b9c2d2"/>
    </svg>
    <span class="brand-name on-blue" style="left:220px;top:32px;font-size:5.5px">Laufbahnwechsel.de</span>
  </section>

  <!-- Open envelope -->
  <section class="piece envelope-open">
    <svg width="440" height="282" viewBox="0 0 440 282" aria-hidden="true">
      <path d="M21 10 Q24 0 35 0 H405 Q416 0 419 10 L440 62 H0 Z" fill="var(--blue)"/>
      <rect x="0" y="62" width="440" height="220" fill="var(--paper)"/>
      <path d="M0 62 H440 L418 116 Q414 123 404 123 H36 Q26 123 22 116 Z" fill="var(--blue)"/>
      <rect x="0" y="61.5" width="440" height="1" fill="#3a4f70"/>
    </svg>
  </section>

</div>
</body>
</html>
```